Need webdesign for service company that provides Car hiring service and transit service

We need a web design for a company that provides airport transit services and transport services including Limo, Corporate cars, Disability transit, Family transit service. We need is a simple and professional design.

Below is site which we like and also offer the same service http://www.ridelarkway.com.au/
Updates

Project Deadline Extended
Reason: Waiting for the Feedback from multiple stakeholders. Need the time to select and approve the design

Target Market(s)

Tourism, Travel

Industry/Entity Type

Airport

Number of Pages Required

3 page

Font styles to use
Decorative
Script

Requirements
Must have
• Simple and Professional, Site we like http://www.ridelarkway.com.au/ and also need to mobile friendly
Should not have
• Shouldn't have too many images

```html
<!DOCTYPE html>
<html lang="en">
<head>
<meta charset="utf-8">
<title>Rydewell – Private &amp; Business Transport</title>
<link href="https://fonts.googleapis.com/css2?family=Raleway:wght@300;400;600;700;800&family=Arimo:wght@400&display=swap" rel="stylesheet">
<style>
:root{
  --ink:#4a4a4f;
  --muted:#7a7a80;
  --panel:#525257;
  --line:#e3e3e6;
  --orange-top:#ff8a00;
  --orange-bottom:#ff6a00;
  --blue:#2a6aa8;
  --footer:#535356;
  --white:#ffffff;
}
*{box-sizing:border-box;margin:0;padding:0}
html,body{width:1200px;height:1081px;overflow:hidden}
body{position:relative;font-family:"Arimo",Arial,sans-serif;color:var(--ink);background:#f0f0f2}
.abs{position:absolute}
.site-header{left:0;top:0;width:1200px;height:98px;background:var(--white);border-bottom:1px solid var(--line)}
.brand{left:85px;top:26px;display:flex;align-items:center;gap:10px;font-family:"Raleway",sans-serif;font-weight:600;font-size:32px;color:#333;letter-spacing:.5px}
.brand-mark{width:36px;height:36px;border:3px solid #222;border-radius:50%}
.header-icons{right:85px;top:40px;display:flex;gap:24px}
.hero{left:0;top:99px;width:1200px;height:585px;background:linear-gradient(#f6f6f7,#e9e9eb)}
.hero-title{left:0;width:1200px;text-align:center;font-family:"Raleway",sans-serif}
.hero-title.top{top:139px;font-weight:600;font-size:25px;color:#4b4b50}
.hero-title.sub{top:176px;font-weight:300;font-size:30px;color:#6a6a70}
.quote{left:85px;top:230px;width:333px;height:396px;background:var(--panel)}
.quote h2{position:absolute;left:37px;top:33px;font-family:"Raleway",sans-serif;font-weight:300;font-size:25px;color:var(--white)}
.quote h2 b{font-weight:700}
.field{position:absolute;left:17px;width:300px;height:41px;background:var(--white);display:flex;align-items:center;font-size:12px;color:#888}
.field .ico{width:29px;height:25px;border-right:1px solid #ddd;display:flex;align-items:center;justify-content:center;margin-right:10px}
.option{position:absolute;left:27px;display:flex;align-items:center;gap:13px;font-size:12.5px;color:var(--white)}
.estimate{position:absolute;left:18px;top:294px;width:294px;height:44px;background:linear-gradient(var(--orange-top),var(--orange-bottom));color:var(--white);font-family:"Raleway",sans-serif;font-weight:700;font-size:18px;display:flex;align-items:center;justify-content:center}
.tile{font-family:"Raleway",sans-serif;color:var(--white);display:flex}
.tile b{font-weight:700}
.tile span{font-weight:300}
.t-disability{left:428px;top:230px;width:367px;height:115px;background:linear-gradient(110deg,#6e6f73,#b8b9bc 45%,#8a8b8f);align-items:center;justify-content:center;font-size:27px;gap:8px}
.t-limo{left:428px;top:351px;width:180px;height:164px;background:linear-gradient(160deg,#1a3f8a,#3c6fd0 55%,#0f2452);align-items:flex-end;padding:0 0 12px 20px;font-size:19px}
.t-airport{left:615px;top:351px;width:180px;height:164px;background:#3a3a3c;flex-direction:column;align-items:center;justify-content:center;text-align:center}
.t-airport span{font-size:19px}
.t-airport b{font-size:27px;margin-top:4px}
.t-corporate{left:803px;top:230px;width:311px;height:285px;background:linear-gradient(170deg,#5a86b6,#8aa7c3 40%,#3b3735 70%,#c4652a);align-items:flex-end;justify-content:center;padding-bottom:16px;font-size:19px}
.t-family{left:428px;top:521px;width:367px;height:105px;background:linear-gradient(100deg,#88a7c5,#a9c2d8 50%,#7998b8);flex-direction:column;justify-content:center;padding-left:21px;font-size:19px;line-height:1.4}
.t-other{left:804px;top:521px;width:310px;height:105px;background:var(--blue);align-items:center;justify-content:center;font-size:26px;gap:7px}
.features{left:0;top:684px;width:1200px;height:324px;background:linear-gradient(#e4e4e7,#f7f7f9)}
.feature{width:260px;text-align:center;top:746px}
.feature .ring{width:132px;height:132px;border:1.5px solid #bdbdc2;border-radius:50%;margin:0 auto;display:flex;align-items:center;justify-content:center}
.feature p{margin-top:20px;font-size:12.5px;line-height:24px;color:var(--muted)}
.site-footer{left:0;top:1008px;width:1200px;height:73px;background:var(--footer);color:var(--white);font-size:13.5px}
.copyright{left:85px;top:29px}
.social{right:86px;top:18px;display:flex;gap:7px}
.social i{width:36px;height:36px;border:1.5px solid var(--white);border-radius:50%;display:block}
</style>
</head>
<body>
<header class="site-header abs">
  <div class="brand abs"><span class="brand-mark"></span>RYDEWELL</div>
  <nav class="header-icons abs">
    <svg width="20" height="18" viewBox="0 0 20 18" aria-label="Menu"><g fill="#777"><rect y="1" width="20" height="3.5"/><rect y="7.5" width="20" height="3.5"/><rect y="14" width="20" height="3.5"/></g></svg>
    <svg width="18" height="18" viewBox="0 0 24 24" aria-label="Call"><path fill="#777" d="M6.6 10.8a15 15 0 0 0 6.6 6.6l2.2-2.2c.3-.3.7-.4 1-.2 1.1.4 2.3.6 3.6.6.6 0 1 .4 1 1V20c0 .6-.4 1-1 1A17 17 0 0 1 3 4c0-.6.4-1 1-1h3.5c.6 0 1 .4 1 1 0 1.3.2 2.5.6 3.6.1.3 0 .7-.2 1z"/></svg>
    <svg width="20" height="20" viewBox="0 0 20 20" aria-label="Search"><circle cx="8" cy="8" r="6" fill="none" stroke="#777" stroke-width="3"/><line x1="12.5" y1="12.5" x2="18.5" y2="18.5" stroke="#777" stroke-width="3.5" stroke-linecap="round"/></svg>
  </nav>
</header>

<section class="hero abs"></section>
<h1 class="hero-title top abs">PRIVATE &amp; BUSINESS</h1>
<p class="hero-title sub abs">PERSONALISED TRANSPORT SERVICES</p>

<form class="quote abs">
  <h2>GET INSTANT <b>QUOTE</b></h2>
  <div class="field" style="top:86px"><span class="ico"><svg width="11" height="11"><circle cx="5.5" cy="5.5" r="4.5" fill="none" stroke="#888"/></svg></span>Origin (public Location or Exact Address</div>
  <div class="field" style="top:147px"><span class="ico"><svg width="10" height="14" viewBox="0 0 10 14"><path d="M5 1a4 4 0 0 0-4 4c0 3 4 8 4 8s4-5 4-8a4 4 0 0 0-4-4z" fill="none" stroke="#888" stroke-width="1.3"/><circle cx="5" cy="5" r="1.4" fill="#888"/></svg></span>Destination(Pubilc Location or Exact Address</div>
  <div class="option" style="top:204px"><svg width="13" height="13"><path d="M6.5 1v11M1 6.5h11" stroke="#fff" stroke-width="3"/></svg>ADD STOPS</div>
  <div class="option" style="top:242px"><svg width="15" height="15"><circle cx="7.5" cy="7.5" r="6" fill="none" stroke="#fff" stroke-width="2"/><circle cx="7.5" cy="7.5" r="2.8" fill="#fff"/></svg>SHOW OTHER VEHICLES</div>
  <div class="estimate">ESTIMATE FARE</div>
</form>

<div class="tile t-disability abs" role="img" aria-label="Brushed metal vehicle interior photo"><span>DISABILITY</span><b>TRANSIT</b></div>
<div class="tile t-limo abs" role="img" aria-label="White stretch limousine in front of city skyline photo"><b>LIMO</b></div>
<div class="tile t-airport abs"><span>AIRPORT</span><b>TRANSIT</b></div>
<div class="tile t-corporate abs" role="img" aria-label="Dark executive sedan at sunset photo"><b>CORPORATE CARS</b></div>
<div class="tile t-family abs" role="img" aria-label="Travellers walking through an airport terminal photo"><span>FAMILY</span><b>TRANSIT SERVICE</b></div>
<div class="tile t-other abs"><span>OTHER</span><b>SERVICES</b></div>

<section class="features abs"></section>
<div class="feature abs" style="left:120px">
  <div class="ring"><svg width="38" height="34" viewBox="0 0 38 34"><rect x="1" y="6" width="36" height="27" rx="4" fill="#777"/><rect x="12" y="1" width="14" height="7" rx="2" fill="none" stroke="#777" stroke-width="2.5"/><rect x="7" y="6" width="2" height="27" fill="#e8e8ea"/><rect x="29" y="6" width="2" height="27" fill="#e8e8ea"/></svg></div>
  <p>Executive chauffeur service and airport<br>transfers &amp; corporate limo hire</p>
</div>
<div class="feature abs" style="left:471px">
  <div class="ring"><svg width="36" height="36" viewBox="0 0 36 36"><circle cx="18" cy="18" r="15" fill="none" stroke="#777" stroke-width="4.5"/><path d="M18 9v10h-7" fill="none" stroke="#777" stroke-width="3"/></svg></div>
  <p>Real time booking and confirmation system<br>for all of your limousine services</p>
</div>
<div class="feature abs" style="left:821px">
  <div class="ring"><svg width="44" height="34" viewBox="0 0 44 34"><rect x="2" y="2" width="40" height="30" rx="3" fill="none" stroke="#777" stroke-width="3.5"/><rect x="2" y="9" width="40" height="6" fill="#777"/><rect x="8" y="23" width="5" height="3" fill="#777"/><rect x="15" y="23" width="7" height="3" fill="#777"/></svg></div>
  <p>No credit card surcharge on any of our lim-<br>ousine hire services</p>
</div>

<footer class="site-footer abs">
  <p class="copyright abs">© Copy Right -2017 Rydewell. All rights reserved.</p>
  <div class="social abs"><i></i><i></i><i></i><i></i><i></i></div>
</footer>
</body>
</html>
```